Pre-Paid Card for Teens needs a design

We are a Fintech company called Toqavel. We will sell prepaid cards for families and teens. Now we need a prepaid card design. Prepaid card should have a orbitpay logo, company logo, 16 card number, expire date. Our webpage is http://www.toqavel-example.com
Target Market(s)
Teenages between 8 - 18 years old
Industry/Entity Type
It Company
Requirements
Must have
- The prepaid card must include toqavel logo, orbitpay debit card logo (I already attached a sample card), 16 digit card number and expire date.
Nice to have
- It should be fun and prestigious for young people.
Should not have
- We don't want that the card has a lots of color

```html
<!DOCTYPE html>
<html lang="en">
<head>
<meta charset="utf-8">
<title>Toqavel Prepaid Card</title>
<link rel="stylesheet" href="https://fonts.googleapis.com/css2?family=Fredoka:wght@600&family=Share+Tech+Mono&family=Roboto:wght@700&display=swap">
<style>
  :root {
    --backdrop: #e9e6e3;
    --card: #f2f2f4;
    --purple: #663399;
    --purple-deep: #230d4a;
    --yellow: #f9bc1c;
    --orange: #ee7c24;
    --ink: #111111;
    --badge-line: #1a1a1a;
    --silver: #c4c8cc;
  }
  html, body {
    margin: 0;
    width: 1200px;
    height: 1200px;
    overflow: hidden;
    background: var(--backdrop);
  }
  .prepaid-card {
    position: absolute;
    left: 80px;
    top: 273px;
    width: 1040px;
    height: 654px;
    background: var(--card);
    border-radius: 26px;
    box-shadow: 0 6px 14px rgba(0,0,0,0.18);
    overflow: hidden;
  }
  .brand {
    position: absolute;
    left: 54px;
    top: 42px;
    display: flex;
    align-items: center;
    gap: 24px;
  }
  .brand-dot {
    width: 100px;
    height: 100px;
    border-radius: 50%;
    background: var(--purple);
  }
  .brand-name {
    font-family: "Fredoka", sans-serif;
    font-weight: 600;
    font-size: 66px;
    color: var(--yellow);
    line-height: 1;
  }
  .hero-shape {
    position: absolute;
    left: 620px;
    top: 30px;
    width: 300px;
    height: 300px;
    border-radius: 50%;
    background: var(--purple);
  }
  .card-number {
    position: absolute;
    left: 74px;
    top: 358px;
    font-family: "Share Tech Mono", monospace;
    font-size: 50px;
    line-height: 1;
    letter-spacing: 8px;
    word-spacing: 14px;
    color: var(--ink);
    white-space: nowrap;
  }
  .bin {
    position: absolute;
    left: 76px;
    top: 432px;
    font-family: "Roboto", sans-serif;
    font-weight: 700;
    font-size: 20px;
    line-height: 1;
    color: var(--ink);
  }
  .expiry {
    position: absolute;
    left: 516px;
    top: 432px;
    display: flex;
    align-items: center;
    gap: 40px;
  }
  .expiry-label {
    font-family: "Roboto", sans-serif;
    font-weight: 700;
    font-size: 17px;
    line-height: 1.15;
    color: var(--ink);
  }
  .expiry-date {
    font-family: "Share Tech Mono", monospace;
    font-size: 36px;
    line-height: 1;
    letter-spacing: 6px;
    color: var(--ink);
  }
  .features {
    position: absolute;
    left: 74px;
    top: 522px;
    display: flex;
    gap: 12px;
  }
  .feature-icon {
    width: 86px;
    height: 86px;
  }
  .network-badge {
    position: absolute;
    left: 814px;
    top: 356px;
    width: 186px;
    height: 244px;
    box-sizing: border-box;
    border: 3px solid var(--badge-line);
    border-radius: 42px;
    display: flex;
    flex-direction: column;
    align-items: center;
    justify-content: space-around;
    padding: 14px 0;
  }
  .debit-patch {
    width: 160px;
    height: 100px;
    border-radius: 50px;
    background: linear-gradient(135deg, #e3e6e8, var(--silver));
  }
  .network-name {
    font-family: "Fredoka", sans-serif;
    font-weight: 600;
    font-size: 40px;
    line-height: 1;
    color: var(--purple-deep);
  }
</style>
</head>
<body>
  <main class="prepaid-card">
    <div class="hero-shape" role="img" aria-label="Brand decoration"></div>

    <div class="brand">
      <div class="brand-dot"></div>
      <span class="brand-name">toqavel</span>
    </div>

    <div class="card-number">5157 5500 0000 0000</div>
    <div class="bin">5157</div>

    <div class="expiry">
      <div class="expiry-label">VALID<br>THRU</div>
      <div class="expiry-date">10/20</div>
    </div>

    <div class="features">
      <svg class="feature-icon" viewBox="0 0 86 86" aria-label="Send money">
        <circle cx="43" cy="43" r="43" fill="var(--orange)"/>
        <rect x="22" y="30" width="42" height="28" rx="3" fill="#fff"/>
        <path d="M22 32 L43 48 L64 32" fill="none" stroke="var(--orange)" stroke-width="3"/>
      </svg>
      <svg class="feature-icon" viewBox="0 0 86 86" aria-label="Mobile app">
        <circle cx="43" cy="43" r="43" fill="var(--orange)"/>
        <rect x="31" y="20" width="24" height="46" rx="4" fill="#fff"/>
        <rect x="34" y="26" width="18" height="30" fill="var(--orange)"/>
        <circle cx="43" cy="61" r="2.5" fill="var(--orange)"/>
      </svg>
      <svg class="feature-icon" viewBox="0 0 86 86" aria-label="Savings">
        <circle cx="43" cy="43" r="43" fill="var(--orange)"/>
        <rect x="22" y="40" width="42" height="24" rx="4" fill="#fff"/>
        <rect x="35" y="44" width="16" height="3" rx="1.5" fill="var(--orange)"/>
        <circle cx="43" cy="28" r="8" fill="#fff"/>
      </svg>
      <svg class="feature-icon" viewBox="0 0 86 86" aria-label="Wallet">
        <circle cx="43" cy="43" r="43" fill="var(--orange)"/>
        <rect x="20" y="30" width="44" height="32" rx="4" fill="#fff"/>
        <rect x="50" y="40" width="16" height="12" rx="3" fill="var(--orange)"/>
        <circle cx="56" cy="46" r="2.5" fill="#fff"/>
      </svg>
    </div>

    <div class="network-badge">
      <div class="debit-patch"></div>
      <span class="network-name">orbitpay</span>
    </div>
  </main>
</body>
</html>
```